Modern, traditional Catering Menu for hotel and conference centre

Modernization of Catering menu while still making this very legible and clear to all guests. Template required in Microsoft word document so that updates to menu items can be easily updated. Menu needs style relatable to hotel and conference centre in an area known for apples, farming and awe-inspiring landscape.

Target Market(s)

Conference and meeting groups,

Industry/Entity Type

Hospitality

Font styles to use
Serif
Script

Colors

Designer to choose colors to be used in the design.

Requirements
Must have
• Legible and clear headers and modern look.
• Microsoft word template to easily be able to make updates.
Nice to have
• Something unique related to apples and our logo

```html
<!DOCTYPE html>
<html lang="en">
<head>
<meta charset="utf-8">
<title>Harvest Ridge Inn – Our Facility</title>
<link rel="stylesheet" href="https://fonts.googleapis.com/css2?family=Tinos:ital,wght@0,400;0,700;1,400;1,700&family=Crimson+Text&display=swap">
<style>
  :root {
    --canvas-bg: #e9eaeb;
    --paper: #ffffff;
    --ink: #111111;
    --brand: #2b1210;
    --accent: #c8802e;
    --frame: #e0b98e;
    --muted: #8a8a8a;
  }
  * { margin: 0; padding: 0; box-sizing: border-box; }
  html, body { width: 1200px; height: 1200px; overflow: hidden; }
  body { background: var(--canvas-bg); font-family: "Tinos", "Times New Roman", serif; color: var(--ink); }
  .page { position: absolute; left: 126px; top: 0; width: 948px; height: 1200px; background: var(--paper); }
  .brand-name { position: absolute; top: 36px; left: 0; width: 100%; text-align: center; font-size: 38px; font-weight: 700; color: var(--brand); letter-spacing: 0.5px; }
  .brand-tagline { position: absolute; top: 86px; left: 0; width: 100%; text-align: center; font-family: "Crimson Text", serif; font-size: 16px; color: var(--accent); }
  .divider { position: absolute; top: 116px; left: 277px; width: 392px; height: 20px; }
  .frame { position: absolute; left: 0; top: 0; width: 948px; height: 1200px; }
  .section-title { position: absolute; top: 195px; left: 0; width: 100%; text-align: center; font-size: 28px; font-weight: 700; }
  .intro { position: absolute; top: 243px; left: 54px; width: 820px; font-size: 15.2px; line-height: 17.6px; }
  .intro em { font-style: italic; }
  .essentials-heading { position: absolute; top: 330px; left: 54px; width: 839px; font-size: 24.5px; font-weight: 700; font-style: italic; padding-bottom: 4px; border-bottom: 1.3px solid var(--ink); }
  .essentials-list { position: absolute; top: 381px; left: 109px; list-style: none; font-size: 15.3px; }
  .essentials-list li { height: 32.6px; line-height: 18px; }
  .contact { position: absolute; top: 1104px; left: 0; width: 100%; text-align: center; font-family: "Crimson Text", serif; font-size: 16.6px; line-height: 18px; color: var(--muted); }
  .contact span { margin: 0 13px; }
</style>
</head>
<body>
<main class="page">
  <header>
    <h1 class="brand-name">Harvest Ridge Inn</h1>
    <p class="brand-tagline">Hotel &amp; Conference Centre | Conference Groups Ridgeview Hall</p>
    <svg class="divider" viewBox="0 0 392 20">
      <line x1="0" y1="3" x2="392" y2="3" stroke="#c8802e" stroke-width="1.5"/>
      <line x1="0" y1="10" x2="120" y2="10" stroke="#c8802e" stroke-width="1.5"/>
      <line x1="272" y1="10" x2="392" y2="10" stroke="#c8802e" stroke-width="1.5"/>
      <rect x="128" y="5" width="136" height="13" rx="6" fill="#e3b98a" role="img" aria-label="Decorative scroll flourish"/>
    </svg>
  </header>

  <svg class="frame" viewBox="0 0 948 1200" aria-hidden="true">
    <path d="M75,168 H873 A40 40 0 0 0 913,208 V1131 A40 40 0 0 0 873,1171 H75 A40 40 0 0 0 35,1131 V208 A40 40 0 0 0 75,168 Z" fill="none" stroke="#e0b98e" stroke-width="4"/>
  </svg>

  <h2 class="section-title">Our Facility</h2>
  <p class="intro"><strong>Harvest Ridge Inn</strong> is truly a landmark of hospitality in the Annapolis Valley of Nova Scotia with 101 Guest Rooms, 29 Seasonal Cabins (May - October) and Conference &amp; Event Centre with over 11,000 sq ft since established in 1972. The grounds sit nestled in one of the many beautiful apple orchards of Ashford. Harvest Ridge Inn overlooks rolling landscapes of Cape Blomidon and the Minas Basin; part of the Bay of Fundy, featuring the world famous highest tides: <em>truly an awe-inspiring view.</em></p>

  <h3 class="essentials-heading">Essentials for your event</h3>
  <ul class="essentials-list">
    <li>Professional Conference Centre</li>
    <li>Heritage Barn, a unique venue onsite offering limited catering</li>
    <li>Free parking</li>
    <li>Complimentary high-speed wireless internet</li>
    <li>Many popular attractions close by including several local wineries</li>
    <li>Parlour guestroom upgrade available to organizers and wedding couples</li>
    <li>Complimentary consultation with one of our Sales Team</li>
    <li>Menu tasting for two with our Chef for a nominal fee</li>
    <li>Guest rooms at a group rate (dependent on number of rooms rented for the occasion)</li>
    <li>Able to accommodate most dietary requirements, please inquire</li>
    <li>Children’s menus available</li>
    <li>Podium &amp; microphone available</li>
    <li>Guest book table, cake table, gift table</li>
    <li>Dance floor available at most venues</li>
    <li>Complimentary bar service (dependent on minimum sales)</li>
    <li>Complimentary cake cutting service, cake knife</li>
    <li>A selection of vases with votive candles for guest tables for a nominal rental fee</li>
    <li>White linen tablecloths and napkins</li>
    <li>Access to the breathtaking grounds for wedding photographs</li>
    <li>Seasonal fireside dining with a year round spectacular view of Cape Blomidon</li>
    <li>Round Table Quiet Lounge</li>
  </ul>

  <footer class="contact">
    <p>Exit 14, Highway 101, 280 Ashford Road North, Ashford, Nova Scotia, B0P 1K0</p>
    <p><span>T: (902) 555 0148</span><span>TF: 1 800 555 0192</span><span>F: (902) 555 0177</span></p>
    <p>Effective: January 1, 2019. All prices are plus 16% gratuity plus applicable taxes and are subject to change.</p>
  </footer>
</main>
</body>
</html>
```